Motel Sign - Front

(21/03/12 - I've edited the brief and removing the words "garden view" its not fitting in the designs I'm getting and just want the word motel to be the focus. I have a template/vision of what I want - see the whiteboard sketch of what I'm looking for uploaded today. Definitely open to creatively, new designs and different ideas but the whiteboard design I've done should be a guideline. Keep it fresh/green/white. use the sample photos of green as inspiration. Thanks)
We are a motel set in the mountain country of Victoria - Australia. The front of the motel needs a fresh look. We recently removed a large amount of the garden to expose a brick courtyard fence which the front of the courtyard faces out to the main road. Within the courtyard fence there is a wooden frame and paneling.
We want to have a new sign created to slot into the wooden frame. (see photo) its the white component.
Its a very large and unusual shape and I want to keep it simple but need to fill the in the best way possible.
The space is 940mm high and 4940mm width.
The message of the sign is simple the word "MOTEL". I want people to be able to drive past and glance in and see we are a motel straight away. So the main purpose of the sign is to say "MOTEL".
I am open to colour use to match the space and have impact. I thought a background colour should be 'off white'. I'm open to the colours used to match your design as long as it matches the brief. Maybe a garden green for the emblem.
IN BRIEF:
1) the word "MOTEL"
2) Border/Background that ties in the garden.
The design should be centred, clean and simple, doesn't have to fill the whole space as long as its balanced and centred.
I like cursive and garden like designs for this one - as long its the word MOTEL still has impact. (OPEN TO NEW IDEAS)
I am also open to different ideas and suggestions if you feel you have a better way to take advantage of this space.
The sign will be 7-8 metres from the road itself.
NOTE: the photos show the space and the painted white in the space where the sign will go. The garden in front of this space will be completely cleared.
Motel

```html
<!DOCTYPE html>
<html lang="en">
<head>
<meta charset="utf-8">
<title>Motel Sign – Front</title>
<link rel="stylesheet" href="https://fonts.googleapis.com/css2?family=Delius&display=swap">
<style>
  :root {
    --paper: #ffffff;
    --frame: #1a1a1a;
    --leaf-light: #b9dc6a;
    --leaf-mid: #8cc63f;
    --leaf-deep: #4fa52e;
    --ink-green: #0f4d16;
    --type-white: #ffffff;
    --garden-dark: #3e4f2a;
    --garden-mid: #7f8d55;
    --brick: #8a5a3c;
    --sky: #c9d3c4;
  }
  * { margin: 0; padding: 0; box-sizing: border-box; }
  html, body {
    width: 1200px;
    height: 686px;
    overflow: hidden;
    background: var(--paper);
  }
  .sheet {
    position: relative;
    width: 1200px;
    height: 686px;
    background: var(--paper);
  }
  .sheet-frame {
    position: absolute;
    left: 21px;
    top: 3px;
    width: 1173px;
    height: 680px;
    border: 2px solid var(--frame);
  }
  .sign-banner {
    position: absolute;
    display: block;
  }
  .sign-banner--main {
    left: 71px;
    top: 22px;
    width: 1079px;
    height: 207px;
  }
  .sign-banner--in-place {
    left: 241px;
    top: 169px;
    width: 402px;
    height: 80px;
  }
  .sign-word {
    font-family: "Delius", "Trebuchet MS", sans-serif;
    fill: var(--type-white);
    stroke: var(--ink-green);
    paint-order: stroke fill;
    stroke-linejoin: round;
  }
  .site-photo {
    position: absolute;
    left: 84px;
    top: 251px;
    width: 747px;
    height: 413px;
    overflow: hidden;
    background:
      linear-gradient(180deg, transparent 0%, transparent 62%, var(--garden-mid) 78%, var(--garden-dark) 100%),
      linear-gradient(180deg, var(--sky) 0%, var(--garden-dark) 18%, var(--brick) 40%, var(--garden-mid) 62%);
  }
</style>
</head>
<body>
<main class="sheet">
  <div class="sheet-frame"></div>

  <svg class="sign-banner sign-banner--main" viewBox="0 0 1079 207" aria-label="MOTEL sign artwork">
    <defs>
      <linearGradient id="leafWash" x1="0" y1="0" x2="1" y2="1">
        <stop offset="0" stop-color="var(--leaf-deep)"/>
        <stop offset="0.35" stop-color="var(--leaf-light)"/>
        <stop offset="0.7" stop-color="var(--leaf-mid)"/>
        <stop offset="1" stop-color="var(--leaf-deep)"/>
      </linearGradient>
    </defs>
    <rect class="sign-ground" width="1079" height="207" fill="url(#leafWash)" role="img" aria-label="Green background with white fern fronds and swirling vine ornaments"/>
    <text class="sign-word" x="539.5" y="172" text-anchor="middle" font-size="190" stroke-width="12" textLength="747" lengthAdjust="spacingAndGlyphs">MOTEL</text>
  </svg>

  <div class="site-photo" role="img" aria-label="Photo of the motel courtyard brick fence with garden shrubs, showing the new green MOTEL sign fitted in place">
    <svg class="sign-banner sign-banner--in-place" viewBox="0 0 402 80" aria-label="MOTEL sign in position">
      <defs>
        <linearGradient id="leafWashSmall" x1="0" y1="0" x2="1" y2="1">
          <stop offset="0" stop-color="var(--leaf-deep)"/>
          <stop offset="0.35" stop-color="var(--leaf-light)"/>
          <stop offset="0.7" stop-color="var(--leaf-mid)"/>
          <stop offset="1" stop-color="var(--leaf-deep)"/>
        </linearGradient>
      </defs>
      <rect width="402" height="80" fill="url(#leafWashSmall)"/>
      <text class="sign-word" x="201" y="67" text-anchor="middle" font-size="72" stroke-width="5" textLength="278" lengthAdjust="spacingAndGlyphs">MOTEL</text>
    </svg>
  </div>
</main>
</body>
</html>
```